Super elegant, crisp & clean Business card design required

We recently upgraded our branding - which is on our website - talvendoraphoto.com

I would like a simple, yet elegant, clean business card design please.

The font of my logo is Cinzel - and because of the natural colour - it's best to have this on a black background.

I would like to have the back of the business card - with simply my logo.

PLEASE DO NOT SUBMIT A COMPLICATED / UNCLEAN DESIGN

Industry/Entity Type

Business

Contact Information for Business Card

Talven Doroshko Photography

Font styles to use
Other font styles liked:
• Cinzel

Requirements
Must have
• A backpage with nothing but my logo
• Simple design - stands out
Should not have
• Colour that dont align with my logo
• Over complicated '/ non symmetrical design

```html
<!DOCTYPE html>
<html lang="en">
<head>
<meta charset="utf-8">
<title>Talven Doroshko Photography – Business Card</title>
<link rel="stylesheet" href="https://fonts.googleapis.com/css2?family=Open+Sans:wght@400;600&display=swap">
<style>
  :root {
    --backdrop: #2b2b2b;
    --card: #111111;
    --card-edge: #1c1c1c;
    --gold: #b39a72;
    --ink: #f2f2f2;
    --rule: #3a3a3a;
  }
  * { box-sizing: border-box; margin: 0; padding: 0; }
  html, body {
    width: 1200px; height: 900px; overflow: hidden;
    background: var(--backdrop);
    font-family: "Open Sans", Arial, sans-serif;
  }
  .stage {
    position: relative; width: 1200px; height: 900px;
    display: flex; align-items: center; justify-content: center; gap: 50px;
  }
  .card {
    position: relative; width: 525px; height: 300px;
    background: var(--card);
    border: 1px solid var(--card-edge);
    border-radius: 22px;
    box-shadow: 0 18px 40px rgba(0,0,0,.45);
  }
  /* front */
  .card-front { display: flex; }
  .brand-panel {
    width: 46%; display: flex; align-items: center; justify-content: center;
    border-right: 1px solid var(--rule); margin: 40px 0;
  }
  .brand-name {
    color: var(--gold); font-weight: 400; font-size: 21px;
    letter-spacing: .08em; text-align: center; line-height: 1.35;
    text-transform: uppercase;
  }
  .contact-panel {
    flex: 1; padding: 48px 0 0 28px; color: var(--ink);
    font-size: 13.5px; line-height: 1.3;
  }
  .person-name { color: var(--gold); font-size: 19px; font-weight: 400; }
  .person-role { margin-bottom: 18px; }
  .address { margin-bottom: 12px; }
  .contact-list { list-style: none; }
  .contact-list li { display: flex; align-items: center; gap: 10px; margin-bottom: 3px; }
  .contact-list svg { width: 11px; height: 11px; flex: none; }
  /* back */
  .card-back { display: flex; align-items: center; justify-content: center; }
  .back-name {
    color: var(--gold); font-weight: 400; font-size: 24px;
    letter-spacing: .1em; text-transform: uppercase; text-align: center; line-height: 1.5;
  }
</style>
</head>
<body>
<main class="stage">
  <section class="card card-front" aria-label="Business card front">
    <div class="brand-panel">
      <p class="brand-name">Talven<br>Doroshko</p>
    </div>
    <div class="contact-panel">
      <p class="person-name">Elias Varnholt</p>
      <p class="person-role">Managing Director</p>
      <p class="address">12345, Address Goes Here<br>Country Name, 123456</p>
      <ul class="contact-list">
        <li>
          <svg viewBox="0 0 12 12" aria-hidden="true"><path fill="#b39a72" d="M2.5 1l2 2-1 1.2c.6 1.4 1.8 2.6 3.3 3.3L8 6.5l2 2-1.3 1.9C5 10 2 7 1.6 3.3z"/></svg>
          <span>(044)-456-7890</span>
        </li>
        <li>
          <svg viewBox="0 0 12 12" aria-hidden="true"><rect x="3" y="1" width="6" height="10" rx="1.2" fill="#b39a72"/><rect x="4" y="2.3" width="4" height="6" fill="#111"/></svg>
          <span>123-456-7890</span>
        </li>
        <li>
          <svg viewBox="0 0 12 12" aria-hidden="true"><rect x="1" y="2.5" width="10" height="7" fill="#b39a72"/><path d="M1 2.5l5 4 5-4" fill="none" stroke="#111" stroke-width="1"/></svg>
          <span>info@youremail.com</span>
        </li>
        <li>
          <svg viewBox="0 0 12 12" aria-hidden="true"><circle cx="6" cy="6" r="5" fill="#b39a72"/><path d="M1 6h10M6 1c-2 2.5-2 7.5 0 10M6 1c2 2.5 2 7.5 0 10" fill="none" stroke="#111" stroke-width=".8"/></svg>
          <span>www.talvendoraphoto.com</span>
        </li>
      </ul>
    </div>
  </section>

  <section class="card card-back" aria-label="Business card back">
    <p class="back-name">Talven Doroshko<br>Photography</p>
  </section>
</main>
</body>
</html>
```